New Company Business Card design

Looking for a corporate looking business card utilising my new logo design - the logo i would like embossed as one option and flat as another - simplistic but stylish - less is more - we are an import export business launching into the market - i would like a couple of options as main background - Grey or Black

```html
<!DOCTYPE html>
<html lang="en">
<head>
<meta charset="utf-8">
<title>Meridian Trade Partners – Business Card</title>
<link rel="stylesheet" href="https://fonts.googleapis.com/css2?family=Roboto:wght@400;500&display=swap">
<style>
  :root {
    --backdrop: #e8e5e1;
    --card-light: #f7f7f6;
    --card-dark: #1a1b1c;
    --brand-blue: #1a78c2;
    --text-grey: #555a5f;
    --divider: #c9c9c9;
    --white: #ffffff;
  }
  * { margin: 0; padding: 0; box-sizing: border-box; }
  html, body {
    width: 1200px; height: 960px; overflow: hidden;
    background: var(--backdrop);
    font-family: "Roboto", Arial, sans-serif;
  }
  .canvas { position: relative; width: 1200px; height: 960px; }

  .card { position: absolute; width: 600px; height: 344px; }
  .card--front { left: 315px; top: 113px; background: var(--card-light); }
  .card--back  { left: 311px; top: 472px; background: var(--card-dark); }

  /* Front */
  .brand-mark {
    position: absolute; left: 70px; top: 140px; width: 230px;
    text-align: center; font-weight: 500; font-size: 64px; line-height: 1;
    color: var(--brand-blue); letter-spacing: 2px;
  }
  .divider {
    position: absolute; left: 310px; top: 99px; width: 1px; height: 145px;
    background: var(--divider);
  }
  .holder { position: absolute; left: 340px; top: 107px; }
  .holder__name {
    font-size: 21px; font-weight: 500; color: var(--brand-blue);
    text-transform: uppercase; line-height: 1.1;
  }
  .holder__title {
    font-size: 14px; color: var(--text-grey); text-transform: uppercase; margin-top: 2px;
  }
  .contact-list { list-style: none; margin-top: 10px; }
  .contact-list li {
    display: flex; align-items: center; height: 19px;
    font-size: 14px; color: var(--text-grey);
  }
  .contact-list svg { width: 14px; height: 14px; margin-right: 9px; fill: var(--brand-blue); }
  .address {
    position: absolute; left: 0; right: 0; top: 297px;
    display: flex; justify-content: center; align-items: center;
    font-size: 14px; color: var(--text-grey);
  }
  .address svg { width: 12px; height: 16px; margin-right: 8px; fill: var(--brand-blue); }

  /* Back */
  .back-mark {
    position: absolute; left: 0; right: 0; top: 88px; text-align: center;
    font-weight: 500; font-size: 72px; line-height: 1; color: var(--white); letter-spacing: 3px;
  }
  .back-name {
    position: absolute; left: 0; right: 0; top: 196px; text-align: center;
    font-size: 20px; font-weight: 500; color: var(--white); letter-spacing: 1px;
    text-transform: uppercase;
  }
  .back-tagline {
    position: absolute; left: 0; right: 0; top: 229px; text-align: center;
    font-size: 9px; color: var(--white); letter-spacing: 2.6px; text-transform: uppercase;
  }
  .back-web {
    position: absolute; left: 0; right: 0; top: 288px; text-align: center;
    font-size: 14px; color: var(--white); letter-spacing: 2.6px;
  }
</style>
</head>
<body>
<main class="canvas">
  <section class="card card--front">
    <div class="brand-mark">MTP</div>
    <div class="divider"></div>
    <div class="holder">
      <p class="holder__name">Daniel Moreau</p>
      <p class="holder__title">CEO/Founder</p>
      <ul class="contact-list">
        <li><svg viewBox="0 0 24 24"><path d="M6.6 10.8a15 15 0 0 0 6.6 6.6l2.2-2.2a1 1 0 0 1 1-.25 11.4 11.4 0 0 0 3.6.57 1 1 0 0 1 1 1V20a1 1 0 0 1-1 1A17 17 0 0 1 3 4a1 1 0 0 1 1-1h3.5a1 1 0 0 1 1 1c0 1.250.2 2.450.57 3.57a1 1 0 0 1-.25 1z"/></svg>555 210 4471</li>
        <li><svg viewBox="0 0 24 24"><path d="M7 1h10a2 2 0 0 1 2 2v18a2 2 0 0 1-2 2H7a2 2 0 0 1-2-2V3a2 2 0 0 1 2-2zm0 3v14h10V4zm5 15.5a1.2 1.2 0 1 0 0 2.4 1.2 1.2 0 0 0 0-2.4z"/></svg>555 318 2096</li>
        <li><svg viewBox="0 0 24 24"><path d="M6 2h12v6H6zM3 9h18a2 2 0 0 1 2 2v7h-4v4H5v-4H1v-7a2 2 0 0 1 2-2zm4 7v4h10v-4z"/></svg>555 742 6630</li>
        <li><svg viewBox="0 0 24 24"><path d="M2 5h20v14H2zm2 2v.5l8 5 8-5V7l-8 5z"/></svg>hello@meridiantrade.com</li>
      </ul>
    </div>
    <p class="address"><svg viewBox="0 0 12 16"><path d="M6 0a6 6 0 0 0-6 6c0 4.5 6 10 6 10s6-5.5 6-10a6 6 0 0 0-6-6zm0 8.3A2.3 2.3 0 1 1 6 3.7a2.3 2.3 0 0 1 0 4.6z"/></svg>214 Harbor View Road Portland, Oregon 97201</p>
  </section>

  <section class="card card--back">
    <div class="back-mark">MTP</div>
    <p class="back-name">Meridian Trade Partners</p>
    <p class="back-tagline">Worldwide supply for every local market</p>
    <p class="back-web">www.meridiantradepartners.com</p>
  </section>
</main>
</body>
</html>
```